UI design for an Zyn(Halvo) photo editing app

This design contest is to design the UI/screenshots of an Zyn(Halvo) app named "Kestrel Pix". Some minor design details are left out at this point as the mockup is still in progress. The icon of this app will be designed separately. The winner of this job will be selected to work on a long term basis as an Dorvo version and several updates will have to be designed as well as the Quillex version. Please take
this as a long term opportunity.
The photo app is called "Kestrel Pix". The design need to dynamic, different that stands out WITH a serious and polished look.
All the mockups and sample screenshots are attached for ease. Please thoroughly review them.
This app has the following screens:
1. Welcome screen(just a simple background will do now as icon will be put later).
2. Main Screen (or LightBox)
The background of this screen can be the same as the background of the welcome screen. It can be a wooden background OR a background of your
choice that fits and blends in the buttons and fonts/colors.
The main screen has this bars/buttons/options that has separate screens:
On top, menu bar:
has these buttons
settings on the left(icon)
in the middle, 3 buttons (please check lightbox mockup and lightbox sample pics)
on the right, share icon(check share screen sample)
Our share options:
"Share" button screenshot:
Our share options:
Save
Email
Copy
Moodlefy
Chatterbay
Zorbly
Quorra
in the middle, just background where the pictures would appear later after importing
or saving
at the bottom bar:
3 buttons:
Camera Roll(on the left)
Camera Button(middle)
Advanced Button(on the right)
2 versions of this screenshot need to be designed.
1. regular version with all the options
2. regular version plus the "steam effect" button showing up on top of the "Advanced" button(mockup with red lines)
3 separate screenshots need to be designed for the options"
settings screenshot(please check sample):
Gift Kestrel Pix to a friend
Rate/review in the Tundle Hub
(space in between...so they are grouped)
Geotagiing(on/off)
Captured photos get location-specific information(these lines in smaller fonts)
Launch in Capture Mode(on/off)
Kestrel Pix is automatically lauched in camera mode
Autosave to Camera Roll(on/off)
Captured photos are directly saved to camera roll
Reset All Tutorials
Tap to reset all the tutorials
In the "Steam Effect" screen, please check the mockup
Top Bar: lightbox button(to go back), heading and Done button
Middle: Steam background(provided)
Bottom bar:
refresh button
droplets(when clicked on/off options show up on top, please check mockup)
finger size(when clicked 3 options show up)
steam density(when clicked 3 options show up)
Please use the buttons for the droplets, finger size and steam density from the steam effects button image provided)
(and also the background of this screenshot(in the middle) would be a steam screen which is provided. Please use the
steam background provided and you need to use the background in the middle, just omit the top and the bottom bar from the image)
Now back to the main(lightbox screen):
When Clicked on the "Camera" in the middle of the bottom bar, the capture mode screen shows up.
Please refer to the mockup first
There you will see the cancel button on the left
camera button in the middle
a small settings button on the right
and a filters button on the right
and the filters bar on the top
ours need to like this
please refer to capture mode sample 1
please refer to capture mode sample 2
please refer to capture mode sample 3
normal
Grid
timer(5/15/30 secs)
Edit Screen(check sample)
Edit options
Adjust:(displayed on a bar)
1. Left
2. Right
3. Horizontal
4. Vertical
5. Straightening
Crop:
None
Original
Golden
Freeform
Square
3:2
4:3
4:6
5:7
8:10
16:9
Filters:(please note that this filter icon and the filter icon in the "capture mode" screenshot need to same)
(the filters are displayed on a bar, please check sample)
There is a sample picture that you need to put in the picture of the filters. It would be same picture in
every filter at this point.
00.None
0.Calibrate
1. aurora
2. drizzle
3. icicle
4. blizzard
5. calm
6. dew
7. knot
8. dry
9. eye
10. flurry
11. fog
12. frost
13. hail
14. haze
15. heat
16. humid
17. overcast
18. polar
19. thermal
20. trace
Editing options on top:(check sample)
Brightness
Contrast
Saturation
Textures:(dispalyed on a bar, check sample)
1.None
2.Bark
3.Grunge1
4.Grunge2
5.grunge3
6.Grunge4
7.Paper
8.Cardboard
9.Wood
10.Bokeh
11.Bricks
12.Metal
13.Asphalt
14.Pavement1
15.Pavement2
16.Paint1
17.Paint2
18.Rust
19.Towel
20.Stone1
21.Stone2
22.Wall
23.Urban1
24.Urban2
25.Urban3
26.Watercolor
Tilt-shift/Vignette:(check sample)
Borders:(check samples, at this point, we are working on them, you just need to make a bar that displays them)
1.None
2.
3.
4.
5.
6.
7.
8.
9.
10.
11.
12.
13.
14.
15.
16.
This is our primary design mockup. Upon selecting the final version, we will be working on some more and minor details(as
we are also working with the coders).
And there is a folder callled "app sample". Please take a look at it and think how our app can be different and stand out.
Thanks and feel free to contact me anytime if you have any questions. Looking forward to hearing from you and building a long term
relationship.
All camera app users who likes to edit their photos with cool tools.
Building

```html
<!DOCTYPE html>
<html lang="en">
<head>
<meta charset="utf-8">
<title>Kestrel Pix – Capture Mode</title>
<link rel="stylesheet" href="https://fonts.googleapis.com/css2?family=Roboto:wght@500;700&display=swap">
<style>
  :root {
    --bar-red: #a30f12;
    --bar-red-dark: #7d0a0c;
    --stitch: #d9696b;
    --slider-red: #c2161b;
    --track-light: #f2f2f2;
    --track-edge: #9a9a9a;
    --icon-light: #f1f1f1;
    --icon-shade: #b9b9b9;
    --popup-grey: #c9c9c9;
    --popup-edge: #8f8f8f;
    --label: #f4f4f4;
    --cancel-text: #7a0c0e;
  }
  * { box-sizing: border-box; margin: 0; padding: 0; }
  html, body { width: 676px; height: 1200px; overflow: hidden; background: #000; }
  .capture-screen {
    position: relative;
    width: 676px; height: 1200px;
    font-family: "Roboto", Arial, sans-serif;
  }
  .viewfinder {
    position: absolute; left: 0; top: 0; width: 676px; height: 1075px;
    background:
      linear-gradient(180deg, rgba(160,40,40,.35) 0 6%, transparent 6%),
      radial-gradient(ellipse at 75% 55%, #0d0d0f 0 35%, transparent 60%),
      linear-gradient(180deg, #d9d9d2 0%, #bdbcb6 30%, #8c8a86 62%, #4a4845 82%, #2a2927 100%);
  }
  .zoom-label {
    position: absolute; left: 36px; top: 957px;
    color: var(--label); font-weight: 700; font-size: 21px;
    text-shadow: 0 1px 2px rgba(0,0,0,.6);
  }
  .zoom-slider { position: absolute; left: 100px; top: 954px; }
  .bottom-bar {
    position: absolute; left: 0; top: 1075px; width: 676px; height: 125px;
    background: linear-gradient(180deg, var(--bar-red) 0%, var(--bar-red-dark) 100%);
    border-top: 2px solid #5e0708;
  }
  .bottom-bar::before {
    content: ""; position: absolute; left: 0; right: 0; top: 7px;
    border-top: 2px dashed var(--stitch); opacity: .7;
  }
  .cancel-button {
    position: absolute; left: 30px; top: 36px; width: 90px; height: 48px;
    border-radius: 8px;
    background: linear-gradient(180deg, #ffffff 0%, #d6d6d6 100%);
    border: 1px solid #5a5a5a;
    color: var(--cancel-text); font-weight: 700; font-size: 21px;
    display: flex; align-items: center; justify-content: center;
  }
  .shutter-button { position: absolute; left: 270px; top: 12px; }
  .filters-button { position: absolute; left: 463px; top: 32px; }
  .settings-button { position: absolute; left: 597px; top: 31px; }
  .capture-options { position: absolute; left: 516px; top: 990px; }
</style>
</head>
<body>
<main class="capture-screen">
  <div class="viewfinder" role="img" aria-label="Live camera preview of an office desk with a laptop, cables and a phone"></div>

  <span class="zoom-label">1.5x</span>
  <svg class="zoom-slider" width="538" height="32" viewBox="0 0 538 32" aria-label="Zoom slider">
    <rect x="1" y="2" width="536" height="28" rx="14" fill="var(--track-light)" stroke="var(--track-edge)" stroke-width="2"/>
    <rect x="9" y="10" width="520" height="12" rx="6" fill="#ffffff" stroke="#cfcfcf"/>
    <rect x="174" y="10" width="355" height="12" rx="6" fill="var(--slider-red)"/>
    <rect x="164" y="5" width="14" height="22" rx="3" fill="#e8e8e8" stroke="#777" stroke-width="1.5"/>
    <line x1="169" y1="10" x2="169" y2="22" stroke="#888"/>
    <line x1="173" y1="10" x2="173" y2="22" stroke="#888"/>
  </svg>

  <svg class="capture-options" width="160" height="85" viewBox="0 0 160 85" aria-label="Capture options: timer, delay, grid">
    <path d="M2 42 Q10 20 40 14 L140 0 Q160 -2 160 10 L160 40 Q150 42 128 46 L115 58 L108 82 L104 50 L40 62 Q12 66 2 42 Z" fill="var(--popup-grey)" stroke="var(--popup-edge)" stroke-width="2"/>
    <line x1="58" y1="14" x2="66" y2="56" stroke="var(--popup-edge)" stroke-width="1.5"/>
    <line x1="104" y1="6" x2="108" y2="50" stroke="var(--popup-edge)" stroke-width="1.5"/>
    <g stroke="#fff" stroke-width="2.5" fill="none">
      <circle cx="31" cy="44" r="10" fill="#666"/>
      <path d="M31 38 V44 L36 47"/>
      <circle cx="81" cy="30" r="11" fill="#666"/>
      <path d="M81 23 V30 L87 33"/>
    </g>
    <g stroke="#eee" stroke-width="1.5" fill="#666">
      <rect x="118" y="16" width="24" height="24"/>
      <path d="M126 16 V40 M134 16 V40 M118 24 H142 M118 32 H142" fill="none"/>
    </g>
  </svg>

  <footer class="bottom-bar">
    <div class="cancel-button">Cancel</div>

    <svg class="shutter-button" width="84" height="80" viewBox="0 0 84 80" aria-label="Take photo">
      <rect x="4" y="14" width="76" height="62" rx="12" fill="none" stroke="var(--icon-light)" stroke-width="4"/>
      <path d="M26 14 V6 Q26 3 30 3 H54 Q58 3 58 6 V14" fill="none" stroke="var(--icon-light)" stroke-width="4"/>
      <circle cx="42" cy="46" r="21" fill="none" stroke="var(--icon-light)" stroke-width="4"/>
      <circle cx="42" cy="46" r="12" fill="none" stroke="var(--icon-shade)" stroke-width="4"/>
    </svg>

    <svg class="filters-button" width="50" height="50" viewBox="0 0 50 50" aria-label="Filters">
      <circle cx="25" cy="25" r="22" fill="none" stroke="var(--icon-light)" stroke-width="3"/>
      <circle cx="25" cy="25" r="9" fill="var(--bar-red)" stroke="var(--icon-light)" stroke-width="3"/>
      <g stroke="var(--icon-light)" stroke-width="3">
        <line x1="25" y1="3" x2="25" y2="16"/>
        <line x1="25" y1="34" x2="25" y2="47"/>
        <line x1="3" y1="25" x2="16" y2="25"/>
        <line x1="34" y1="25" x2="47" y2="25"/>
      </g>
    </svg>

    <svg class="settings-button" width="52" height="52" viewBox="0 0 52 52" aria-label="Settings">
      <g fill="var(--icon-light)">
        <circle cx="26" cy="26" r="17"/>
        <rect x="21" y="2" width="10" height="48" rx="2"/>
        <rect x="21" y="2" width="10" height="48" rx="2" transform="rotate(45 26 26)"/>
        <rect x="21" y="2" width="10" height="48" rx="2" transform="rotate(90 26 26)"/>
        <rect x="21" y="2" width="10" height="48" rx="2" transform="rotate(135 26 26)"/>
      </g>
      <circle cx="26" cy="26" r="8" fill="var(--bar-red)"/>
    </svg>
  </footer>
</main>
</body>
</html>
```